wardrobe/costume stylist needs good business card for own business

Hi:)

I'm wanting a business card for my company. I am a freelance stylist.

I do wardrobe/costume stylist to TV commercials; Films; Fashion and Lifestyle shoots.

I'd like a design based around my name Rosalind Parfrey written nicely, maybe a colour? Up to you?!

I've attached a couple of images of business cards I like
.... be creative and have fun!

Thank you :)

Reason: I was trying to get my new business card ready for before I headed overseas Friday morning but I don't think that was realistic so I'd like to extend the deadline to give time to the project. Thank you

Hi designers:) Thank you for all your designs, I've extended the deadline until Sunday, so there's a bit more time. I've attached 3 pictures of business cards which I quite like, please take a look to see if it can be of help in your process. I like the pale plain or patterned background with dark font and the dark plain or patterned background with the pale font the motifs the feminine fonts the plain fonts I like the idea of playing with a circle or some shape on one side of the card with my name or initials as in the picture I have on my post could you play around with this idea a bit please? Thank you all for the work you've done :) Rosa

Hi I am working overseas til Saturday night sorry for no feedback until I teturn Thanks :) Rosa

Hi designers, Thank you all so much for submitting your designs, I really appreciate your input into my project :) I'm sorry I didn't get to respond to some comments, and give feedback. I didn't back from being away until later than I expected, and the deadline had passed then, so apologies. Thanks to you all again for all your really good designs :) Rosa

Target Market(s)

I am a freelance stylist my target audience is producers, production companies, photographers, directors...

Industry/Entity Type

Business

Requirements
Must have
• Rosalind Parfrey
Stylist or Wardrobe Stylist

email rosaparfrey@mailbox-example.co.nz
Mobile 0218467193

(Don't have to use the words 'email' and 'mobile')
Nice to have
• Would like it to be double sided
Like B & W
Like pale colour background with dark font or white font
Like dark colour background with pale font
Should not have
• I would prefer it not to incorporate pictures

```html
<!DOCTYPE html>
<html lang="en">
<head>
<meta charset="utf-8">
<title>Rosalind Parfrey – Wardrobe Stylist Business Card</title>
<link rel="stylesheet" href="https://fonts.googleapis.com/css2?family=Marcellus&family=Tenor+Sans&display=swap">
<style>
  :root {
    --page-bg: #ffffff;
    --mint: #b3e2cd;
    --mint-light: #c9ecdc;
    --mint-deep: #9dd8bd;
    --ink: #111111;
    --ornament: #1a1f1d;
  }
  * { margin: 0; padding: 0; box-sizing: border-box; }
  html, body {
    width: 1200px;
    height: 900px;
    overflow: hidden;
    background: var(--page-bg);
  }
  .canvas {
    position: relative;
    width: 1200px;
    height: 900px;
  }
  .card {
    position: absolute;
    top: 290px;
    width: 540px;
    height: 310px;
    border-radius: 26px;
    background: var(--mint);
    padding: 7px;
  }
  .card--front { left: 40px; }
  .card--back { left: 620px; }
  .card__frame {
    position: relative;
    width: 100%;
    height: 100%;
    border: 6px solid var(--ink);
    border-radius: 22px;
    overflow: hidden;
    background: var(--mint);
  }
  .card__pattern {
    position: absolute;
    inset: 0;
    background:
      radial-gradient(ellipse at 20% 30%, var(--mint-light) 0%, transparent 55%),
      radial-gradient(ellipse at 80% 70%, var(--mint-light) 0%, transparent 55%),
      linear-gradient(135deg, var(--mint-deep), var(--mint) 50%, var(--mint-deep));
  }
  .card__content {
    position: absolute;
    inset: 0;
    display: flex;
    flex-direction: column;
    align-items: center;
    justify-content: center;
  }
  .ornament {
    background: var(--ornament);
    border-radius: 14px 14px 4px 4px;
  }
  .ornament--bottom { border-radius: 4px 4px 14px 14px; }
  .card--front .ornament { width: 140px; height: 44px; }
  .card--back .ornament { width: 74px; height: 24px; border-radius: 10px 10px 3px 3px; }
  .card--back .ornament--bottom { border-radius: 3px 3px 10px 10px; }
  .brand-name {
    font-family: "Marcellus", serif;
    color: var(--ink);
    font-weight: 400;
    line-height: 1;
    white-space: nowrap;
  }
  .brand-role {
    font-family: "Tenor Sans", sans-serif;
    color: var(--ink);
    text-transform: none;
    white-space: nowrap;
  }
  .card--front .brand-name { font-size: 46px; margin-top: 8px; }
  .card--front .brand-role { font-size: 15px; letter-spacing: 7px; margin: 2px 0 8px; }
  .card--back .card__content { justify-content: flex-start; padding-top: 24px; }
  .card--back .brand-name { font-size: 25px; margin-top: 6px; }
  .card--back .brand-role { font-size: 9px; letter-spacing: 4px; margin: 1px 0 6px; }
  .contact {
    margin-top: 44px;
    text-align: center;
    font-family: "Tenor Sans", sans-serif;
    color: var(--ink);
    font-size: 15px;
    letter-spacing: 2.5px;
    line-height: 1.5;
  }
  .contact__phone { letter-spacing: 4px; }
</style>
</head>
<body>
<main class="canvas">
  <section class="card card--front">
    <div class="card__frame">
      <div class="card__pattern" role="img" aria-label="Pale mint damask floral pattern background"></div>
      <div class="card__content">
        <div class="ornament" role="img" aria-label="Black baroque flourish ornament"></div>
        <h1 class="brand-name">Rosalind Parfrey</h1>
        <p class="brand-role">Wardrobe Stylist</p>
        <div class="ornament ornament--bottom" role="img" aria-label="Black baroque flourish ornament"></div>
      </div>
    </div>
  </section>

  <section class="card card--back">
    <div class="card__frame">
      <div class="card__content">
        <div class="ornament" role="img" aria-label="Small black baroque flourish ornament"></div>
        <h2 class="brand-name">Rosalind Parfrey</h2>
        <p class="brand-role">Wardrobe Stylist</p>
        <div class="ornament ornament--bottom" role="img" aria-label="Small black baroque flourish ornament"></div>
        <address class="contact" style="font-style:normal">
          <div class="contact__phone">0218467193</div>
          <div class="contact__email">rosaparfrey@mailbox-example.co.nz</div>
        </address>
      </div>
    </div>
  </section>
</main>
</body>
</html>
```